One piece Trade show banner, 8' x 8' square

One piece banner for trade show
8' x 8' airborne geophysical company

Target Market(s)

Business

Industry/Entity Type

mineral exploration and science

Colors
0054AA
0677BA
7BADD7
CADEEF
E8F1F8
FFC000
F8CF3A
FAE287
FDF2CF
FEFAEE

Requirements
Must have
• Company logo (attached), slogan (Airborne Geophysics for Discovery). We are looking for a new banner, for a standard 8 x 8' square one-piece booth. I have attached some pictures, our logo, our old banner for reference, and two examples from unrelated companies from a tradeshow that we like. If its possible I'd like to change the color of the helicopter from green to dark grey. IE, keep the orange and white, just change green to dark grey. Looking for a simple, clean design with minimal text.
Nice to have
• I have attached examples of banners that we like (2xIMG), plus our old 3-piece banner r.
Should not have
• Green in the helicopter. Please change the color of the helicopter with green/orange/white to dark grey/orange/white. IE change the green to dark grey and leave the orange and white alone. I've attached lots of pictures but I don't expect them all to be used.

```html
<!DOCTYPE html>
<html lang="en">
<head>
<meta charset="utf-8">
<title>Airborne Geophysics for Discovery – Trade Show Banner</title>
<link rel="stylesheet" href="https://fonts.googleapis.com/css2?family=Bebas+Neue&display=swap">
<style>
  :root {
    --backdrop: #222222;
    --orange: #F98E0F;
    --sun: #FBA81E;
    --ink: #232323;
    --headline-light: #EEF5EE;
    --band-white: #FFFFFF;
    --rock: #8C8782;
    --rock-warm: #A48E82;
    --water: #17A0C8;
    --water-deep: #0A86B4;
  }
  html, body {
    margin: 0;
    width: 1200px;
    height: 1200px;
    overflow: hidden;
    background: var(--backdrop);
  }
  .banner {
    position: absolute;
    left: 173px;
    top: 168px;
    width: 856px;
    height: 856px;
    background: var(--orange);
    overflow: hidden;
    font-family: "Bebas Neue", "Oswald", sans-serif;
  }
  .banner-art {
    position: absolute;
    inset: 0;
    width: 100%;
    height: 100%;
    display: block;
  }
  .slogan-line {
    position: absolute;
    left: 0;
    width: 558px;
    margin: 0;
    text-align: center;
    font-size: 106px;
    line-height: 1;
    font-weight: 400;
    letter-spacing: 1px;
    white-space: nowrap;
  }
  .slogan-line--light { color: var(--headline-light); }
  .slogan-line--dark { color: var(--ink); }
  .slogan-line--one { top: 73px; }
  .slogan-line--two { top: 171px; }
  .slogan-line--three { top: 268px; }

  .brand {
    position: absolute;
    right: 50px;
    top: 42px;
    text-align: right;
    color: var(--ink);
    font-weight: 400;
    line-height: 1;
  }
  .brand-name {
    display: block;
    font-size: 80px;
    letter-spacing: 2px;
  }
  .brand-sub {
    display: block;
    font-size: 30px;
    letter-spacing: 2px;
    margin-top: -12px;
  }
</style>
</head>
<body>
  <section class="banner">
    <svg class="banner-art" viewBox="0 0 1378 1378" preserveAspectRatio="none" aria-hidden="false">
      <defs>
        <linearGradient id="sceneTones" x1="0" y1="0" x2="0" y2="1">
          <stop offset="0" stop-color="var(--rock)"/>
          <stop offset="0.5" stop-color="var(--rock-warm)"/>
          <stop offset="0.62" stop-color="var(--rock)"/>
          <stop offset="0.66" stop-color="var(--water)"/>
          <stop offset="1" stop-color="var(--water-deep)"/>
        </linearGradient>
      </defs>
      <circle class="sun-disc" cx="314" cy="810" r="177" fill="var(--sun)"/>
      <path class="wave-white" fill="var(--band-white)"
        d="M0,850 C200,960 450,910 680,760 C880,620 1060,510 1200,510 C1290,510 1350,560 1378,650 L1378,1378 L0,1378 Z"/>
      <path class="survey-scene" fill="url(#sceneTones)" role="img"
        aria-label="Photo of a white, orange and dark grey survey helicopter with sensor booms flying low over a turquoise lake beneath a rocky mountainside"
        d="M0,870 C200,990 480,950 720,800 C920,670 1080,570 1200,565 C1290,560 1350,600 1378,650 L1378,1378 L0,1378 Z"/>
      <path class="wave-dark" fill="var(--ink)"
        d="M0,818 C200,920 400,900 620,800 C850,680 1000,500 1210,460 C1040,480 880,620 680,760 C450,910 200,960 0,850 Z"/>
    </svg>

    <h1 class="slogan">
      <span class="slogan-line slogan-line--light slogan-line--one">Airborne</span>
      <span class="slogan-line slogan-line--light slogan-line--two">Geophysics</span>
      <span class="slogan-line slogan-line--dark slogan-line--three">For Discovery</span>
    </h1>

    <div class="brand">
      <span class="brand-name">Vantage</span>
      <span class="brand-sub">AeroSurveys</span>
    </div>
  </section>
</body>
</html>
```